Small legal and financial translation company needs Squarespace website, brochure and logo

Hello,
We are Lumarin Services (www.lumarinservices-example.com), a boutique legal and financial translation company. We offer our services mainly to Spanish customers. Our primary line of business is the translation of financial statements, but we translate a wide variety legal and financial texts.
The project we are offering comprises three parts: a redo of the current website, an informational brochure for potential customer and a logo design. These three parts should provide a consistent image. We would develop content soon.
We are looking for a website that would look like a typical law firm website, nothing too fancy. Right now, it is in English, Spanish and French, although the new site need only be in English and Spanish. There must be good toggling between the English and Spanish versions. There would be no need for tie-ins to social media and it would not contain a blog. Basically, a static site. We aren't interesting in driving traffic to the site or SEO, as we will contact nearly all potential customers beforehand. The website must be built in Squarespace to enable a smooth transition. The content would be similar to the current page, we'll be working on the exact content, but a rough draft is attached.
The brochure will be some three pages and would introduce the company to potential customers, using similar images as the website and the logo to be designed.
The only specifications for the logo is, as the website and brochure, it convey a sense of security and trust.
Feel free to ask with any questions as this is the first time we have used this platform.
Thank you!
Updates

I've added a more or less final version for the text in the brochure and updated the brief. Added Wednesday, June 10, 2015

Target Market(s)

Spanish law firms, auditors, accountants, banks, investment firms

Industry/Entity Type

Finance

Logo Text

Lumarin Services

Number of Pages Required

5+ page

Font styles to use
Serif

Requirements
Must have
• The website must be built in Squarespace and have a good option to toggle between English and Spanish versions.
• Brochure must be in both English and Spanish, I'm attaching a rough draft of the information that it will probably have. This should give an idea about what to include and the spacing. I will update it to include the final information.
Nice to have
• Would be nice to have some quality finance- and legal-related images
Should not have
• Vibrant colours

```html
<!DOCTYPE html>
<html lang="en">
<head>
<meta charset="utf-8">
<title>Translation Specialist – Lumarin Services</title>
<link rel="stylesheet" href="https://fonts.googleapis.com/css2?family=Montserrat:wght@400;600;700&family=Oswald:wght@400&family=EB+Garamond:wght@400&display=swap">
<style>
  :root {
    --teal: #2d9ea1;
    --teal-light: #a9dbe8;
    --page-bg: #e6e6e6;
    --body-text: #7a7a7a;
    --menu-text: #7c7c7c;
    --footer-top: #333333;
    --footer-bottom: #1e1e1e;
    --white: #ffffff;
  }
  * { margin: 0; padding: 0; box-sizing: border-box; }
  html, body { width: 1001px; height: 1200px; overflow: hidden; }
  body { position: relative; background: var(--page-bg); font-family: "EB Garamond", Georgia, serif; }

  .hero {
    position: absolute; left: 0; top: 0; width: 1001px; height: 420px;
    background: linear-gradient(160deg, #5a5a5a 0%, #8c8c8c 35%, #b4b4b4 60%, #6e6e6e 100%);
  }
  .brand {
    position: absolute; left: 20px; top: 30px;
    font-family: "Montserrat", Arial, sans-serif; font-weight: 400;
    font-size: 22px; color: var(--teal-light); letter-spacing: 0.5px;
  }
  .top-nav { position: absolute; right: 10px; top: 46px; display: flex; gap: 22px; }
  .top-nav a {
    font-family: "Montserrat", Arial, sans-serif; font-weight: 600;
    font-size: 10px; letter-spacing: 1.2px; color: var(--white); text-decoration: none;
  }
  .hero-title {
    position: absolute; left: 0; top: 166px; width: 1001px; text-align: center;
    font-family: "Montserrat", Arial, sans-serif; font-weight: 700;
    font-size: 46px; line-height: 52px; letter-spacing: 2px; color: var(--white);
  }

  .side-nav { position: absolute; left: 154px; top: 488px; }
  .side-nav .lang { font-size: 18px; color: var(--teal); margin-bottom: 6px; }
  .side-nav ul { list-style: none; }
  .side-nav li {
    font-family: "Oswald", Arial, sans-serif; font-size: 12.5px;
    letter-spacing: 1.6px; line-height: 27.3px; color: var(--menu-text);
  }
  .side-nav li.current { color: var(--teal); }

  .content { position: absolute; left: 341px; top: 488px; width: 520px; }
  .content h1 {
    font-weight: 400; font-size: 27px; line-height: 30px; color: var(--teal); margin-bottom: 20px;
  }
  .content h2 {
    font-weight: 400; font-size: 19px; letter-spacing: 1.2px; color: var(--teal);
    margin-bottom: 9px;
  }
  .content p {
    margin-left: 30px; width: 488px; font-size: 12.6px; line-height: 20.4px;
    color: var(--body-text); margin-bottom: 16px;
  }

  .footer-band { position: absolute; left: 0; top: 1097px; width: 1001px; height: 36px; background: var(--footer-top); }
  .footer-base { position: absolute; left: 0; top: 1133px; width: 1001px; height: 67px; background: var(--footer-bottom); }
</style>
</head>
<body>
  <header class="hero" role="img" aria-label="Black and white photograph of reading glasses and a paper clip resting on legal documents such as a living trust agreement and a pour-over will">
  </header>
  <div class="brand">Lumarin Services</div>
  <nav class="top-nav">
    <a href="#">HOME</a><a href="#">ENGLISH</a><a href="#">SPANISH</a>
  </nav>
  <h1 class="hero-title">TRANSLATION<br>SPECIALIST</h1>

  <nav class="side-nav">
    <div class="lang">English</div>
    <ul>
      <li>WHO WE ARE</li>
      <li>BENEFITS</li>
      <li>LEGAL TRANSLATION</li>
      <li>FINANCIAL TRANSLATION</li>
      <li class="current">TRANSLATION SPECIALIST</li>
      <li>CONTACT</li>
    </ul>
  </nav>

  <main class="content">
    <h1>Benefits of working with a specialist translation company rather than a translation agency:</h1>
    <h2>Quality</h2>
    <p>Translation agencies cannot guarantee that the same translator will always work on your projects, which means customers might receive inconsistent and poorer quality translations depending on the availability of the agency's translators. At Lumarin Services, you personally know who is working on your project and can attest the quality of their work.</p>
    <h2>Pricing</h2>
    <p>Lumarin Services provides the same high-quality services as the leading in-house translation departments in Spain, at a fraction of the price. Our quality control process affords highly polished finished products at reasonable prices. Our low overheads mean that we do not pass on a exorbitant cost structure to our customers. Agencies and the translation departments in Spain's leading law and auditing firms have much higher fixed costs that entail higher prices for the customer.</p>
    <h2>Honesty</h2>
    <p>From time to time, certain projects simply are too big, too urgent or too complex to undertake in the conditions required by our customers. Agencies are capable of handling multi-language projects with ultra-tight deadlines. This inevitably decreases the quality and consistency of our work. We work closely with our customers to set deadlines that ensure quality while respecting the urgency of their affairs.</p>
  </main>

  <div class="footer-band"></div>
  <div class="footer-base"></div>
</body>
</html>
```